Website Development for vaultmerrow.com.au

Build a new Wordpress/Responsive website for vaultmerrow.com.au

Target Market(s)

Compliance Managers, Risk Managers, Information Security and Cyber Security Professionals, Chief Data/Digital Officers, Chief Operating/Financial Officers, Business Continuity Professionals, Disaster Recovery Planners, Small Business Owners, Local/Federal Government entities

Industry/Entity Type

Data Service

Coding

Coded - Design and coding required

Number of Pages Required

5+ page

Font styles to use
Sans Serif

Colors

Designer to choose colors to be used in the design.

Requirements
Must have
• 1. Site Structure: Home Page plus the following chapter-pages for a) Services b) About c) Resources d) Blog e) Contact Us
• 2. Prefer site to built on wordpress and we can purchase a theme if needed (we currently use Kelp9 for other sites)
• 3. Blog needs to be wordpress based
• 4. We will host the site ourselves on our own servers
• 5. Responsive Design
Nice to have
• 1. Livechat capability/interface
• 2. Capability for marketing automation integration (such as hubspot, marketo, infusionsoft etc)
• 3. Capability for CRM integration (Salesforce)

```html
<!DOCTYPE html>
<html lang="en">
<head>
<meta charset="utf-8">
<title>Vaultmerrow — Data Protection Services</title>
<link rel="stylesheet" href="https://fonts.googleapis.com/css2?family=Lato:wght@400;700;900&display=swap">
<style>
:root{
  --red:#e1141f;
  --red-dark:#8d0a12;
  --ink:#1b1b1b;
  --text:#3a3a3a;
  --grey-bg:#f0f0f0;
  --white:#ffffff;
  --black:#111111;
}
*{margin:0;padding:0;box-sizing:border-box}
html,body{width:1200px;height:3557px;overflow:hidden}
body{position:relative;font-family:'Lato',sans-serif;color:var(--text);background:var(--white)}
.abs{position:absolute}
.brand{font-weight:900;color:var(--red);display:flex;align-items:center;gap:12px}
.brand .dot{width:34px;height:34px;background:var(--red);border-radius:50%}
.brand .name{font-size:42px;letter-spacing:1px}
.site-header{left:0;top:0;width:1200px;height:123px;background:var(--white)}
.phone{right:60px;top:18px;font-size:23px;font-weight:700;color:var(--red);display:flex;align-items:center;gap:10px}
.nav a{position:absolute;top:72px;font-size:17px;color:var(--ink);text-decoration:none}
.nav a.active{color:var(--red)}
.hero{left:0;top:123px;width:1200px;height:612px;background:radial-gradient(ellipse at 35% 55%,#7a0b12 0%,#3a0508 45%,#120305 100%)}
.hero-title{left:0;width:1200px;top:357px;text-align:center;font-size:46px;font-weight:400;color:var(--white);letter-spacing:1px}
.hero-text{left:300px;width:600px;top:425px;text-align:center;font-size:15px;line-height:22px;color:var(--white)}
.btn{display:flex;align-items:center;justify-content:center;background:var(--red);color:var(--white);font-weight:900;border-radius:40px;text-transform:uppercase}
.btn-hero{left:500px;top:491px;width:200px;height:57px;font-size:20px}
.btn-sm{width:140px;height:38px;font-size:14px}
.services-card{left:62px;top:667px;width:1079px;height:531px;background:var(--white);box-shadow:0 12px 30px rgba(0,0,0,.12)}
.section-title{font-size:50px;font-weight:400;color:var(--red);text-transform:uppercase}
.services-title{left:0;width:1200px;top:680px;text-align:center}
.arrow{top:695px}
.photo{display:block}
.svc-name{top:983px;font-size:23px;font-weight:900;color:var(--red);text-transform:uppercase}
.svc-text{top:1020px;width:330px;font-size:13.5px;line-height:21px;color:var(--text)}
.body-text{font-size:14.5px;line-height:28px;color:var(--text)}
.blog-band{left:0;top:2158px;width:1200px;height:676px;background:var(--grey-bg)}
.date{left:629px;top:2363px;font-size:13px;letter-spacing:3px;font-weight:700;color:#555}
.blog-head{left:629px;top:2408px;width:340px;font-size:26px;line-height:42px;font-weight:700;color:var(--ink)}
.contact{left:0;top:2834px;width:1200px;height:563px;background:var(--red)}
.contact-title{left:0;width:1200px;top:2900px;text-align:center;font-size:48px;color:var(--white)}
.field{background:var(--white);border:1px solid #ddd;font-size:15px;color:#555;padding:12px 20px}
.btn-submit{left:493px;top:3288px;width:214px;height:59px;border:3px solid var(--white);border-radius:40px;color:var(--white);font-size:24px;font-weight:900;display:flex;align-items:center;justify-content:center;letter-spacing:1px}
.chat{left:1057px;top:3285px;width:86px;height:86px;border-radius:50%;background:var(--black);display:flex;align-items:center;justify-content:center}
.site-footer{left:0;top:3397px;width:1200px;height:160px;background:var(--black)}
.fnav a{position:absolute;top:3432px;font-size:17px;color:var(--white);text-decoration:none}
.social{top:3470px;width:16px;height:16px;border-radius:50%;background:var(--white)}
.copyright{left:901px;top:3503px;font-size:14px;color:var(--white)}
</style>
</head>
<body>

<header class="site-header abs">
  <div class="brand abs" style="left:76px;top:38px"><span class="dot"></span><span class="name">Vaultmerrow</span></div>
  <div class="phone abs">
    <svg width="14" height="20" viewBox="0 0 14 20"><rect x="1" y="1" width="12" height="18" rx="2" fill="none" stroke="#e1141f" stroke-width="2"/><circle cx="7" cy="15" r="1.5" fill="#e1141f"/></svg>
    1-800 555 0142
  </div>
  <nav class="nav">
    <a class="active" style="left:633px">Home</a>
    <a style="left:707px">Services</a>
    <a style="left:800px">About</a>
    <a style="left:880px">Resources</a>
    <a style="left:982px">Blog</a>
    <a style="left:1046px">Contact Us</a>
  </nav>
</header>

<section class="hero abs" role="img" aria-label="Hands typing on a laptop under red light with data protection graphics"></section>
<h1 class="hero-title abs">VAULTMERROW</h1>
<p class="hero-text abs">Lorem ipsum dolor sit amet, consectetur adipiscing elit, sed do eiusmod tempor incididunt ut labore et dolore magna aliqua. Ut enim ad minim veniam, quis nostrud</p>
<div class="btn btn-hero abs">Learn More</div>

<section class="services-card abs"></section>
<h2 class="section-title services-title abs">Our Services</h2>
<svg class="arrow abs" style="left:86px" width="16" height="24" viewBox="0 0 16 24"><path d="M13 3 L4 12 L13 21" fill="none" stroke="#e1141f" stroke-width="4"/></svg>
<svg class="arrow abs" style="left:1098px" width="16" height="24" viewBox="0 0 16 24"><path d="M3 3 L12 12 L3 21" fill="none" stroke="#e1141f" stroke-width="4"/></svg>

<div class="photo abs" style="left:76px;top:761px;width:330px;height:212px;background:linear-gradient(135deg,#c9c3bd,#7a5a3e)" role="img" aria-label="Hand guarding a row of falling wooden blocks"></div>
<div class="photo abs" style="left:434px;top:761px;width:330px;height:212px;background:radial-gradient(circle at 50% 50%,#3fb4ff,#0a2a55 60%,#020a18)" role="img" aria-label="Glowing digital padlock on a circuit background"></div>
<div class="photo abs" style="left:795px;top:761px;width:332px;height:212px;background:linear-gradient(135deg,#9a9a8c,#3b3b35)" role="img" aria-label="Confidential file folders secured with a padlock"></div>

<h3 class="svc-name abs" style="left:76px">Risk Management</h3>
<h3 class="svc-name abs" style="left:434px">Cyber Security</h3>
<h3 class="svc-name abs" style="left:795px">Information Security</h3>
<p class="svc-text abs" style="left:76px">Lorem ipsum dolor sit amet, consectetur adipiscing elit, sed do eiusmod tempor incididunt ut labore et dolore magna aliqua.</p>
<p class="svc-text abs" style="left:434px">Lorem ipsum dolor sit amet, consectetur adipiscing elit, sed do eiusmod tempor incididunt ut labore et dolore magna aliqua.</p>
<p class="svc-text abs" style="left:795px">Lorem ipsum dolor sit amet, consectetur adipiscing elit, sed do eiusmod tempor incididunt ut labore et dolore magna aliqua.</p>
<div class="btn btn-sm abs" style="left:76px;top:1103px">Read More</div>
<div class="btn btn-sm abs" style="left:436px;top:1103px">Read More</div>
<div class="btn btn-sm abs" style="left:797px;top:1103px">Read More</div>

<div class="abs" style="left:76px;top:1297px;width:503px;height:363px;background:var(--red)"></div>
<div class="photo abs" style="left:95px;top:1316px;width:503px;height:368px;background:linear-gradient(135deg,#d8c7b0,#8a5a33 70%,#3a2414)" role="img" aria-label="Hand stopping a line of falling dominoes"></div>
<h2 class="section-title abs" style="left:614px;top:1305px">About Us</h2>
<p class="body-text abs" style="left:614px;top:1376px;width:500px">Lorem ipsum dolor sit amet, consectetur adipiscing elit, sed do eiusmod tempor incididunt ut labore et dolore magna aliqua. Ut enim ad minim veniam, quis nostrud exercitation ullamco laboris nisi ut aliquip ex ea commodo consequat. Duis aute irure dolor in reprehenderit in voluptate velit esse cillum dolore eu fugiat nulla pariatur. Excepteur sint occaecat cupidatat non proident, sunt in culpa qui officia deserunt mollit anim id est laborum.</p>
<div class="btn btn-sm abs" style="left:614px;top:1577px">Read More</div>

<h2 class="section-title abs" style="left:76px;top:1756px">Resources</h2>
<p class="body-text abs" style="left:80px;top:1829px;width:505px">Lorem ipsum dolor sit amet, consectetur adipiscing elit, sed do eiusmod tempor incididunt ut labore et dolore magna aliqua. Ut enim ad minim veniam, quis nostrud exercitation ullamco laboris nisi ut aliquip ex ea commodo consequat. Duis aute irure dolor in reprehenderit in voluptate velit esse cillum dolore eu fugiat nulla pariatur. Excepteur sint occaecat cupidatat non proident, sunt in culpa qui officia deserunt mollit anim id est laborum.</p>
<div class="btn btn-sm abs" style="left:83px;top:2030px">Read More</div>
<div class="abs" style="left:621px;top:1717px;width:506px;height:370px;background:var(--red)"></div>
<div class="photo abs" style="left:605px;top:1739px;width:505px;height:365px;background:linear-gradient(135deg,#dfe6ee,#5a6f88 55%,#1c2430)" role="img" aria-label="Technician with a laptop working at server racks"></div>

<section class="blog-band abs"></section>
<h2 class="section-title abs" style="left:0;width:1200px;top:2204px;text-align:center;font-size:46px">Blog</h2>
<p class="abs" style="left:0;top:2408px;width:142px;font-size:26px;line-height:42px;font-weight:700;color:var(--ink);text-align:right;white-space:nowrap;direction:rtl;overflow:hidden">r sit amet con-<br>g elit, sed do</p>
<p class="abs" style="left:0;top:2517px;width:142px;font-size:14px;line-height:32px;color:var(--text);overflow:hidden;white-space:nowrap;direction:rtl">adipisicing<br>cididunt ut labore et<br>.</p>
<div class="photo abs" style="left:230px;top:2301px;width:339px;height:457px;background:linear-gradient(160deg,#6b7078,#b9b4ac 55%,#e3a7c9)" role="img" aria-label="Team arranging sticky notes on a planning table"></div>
<div class="date abs">DATE : 12-02-2019</div>
<h3 class="blog-head abs">Lorem ipsum dolor sit amet consectetur adipisicing elit, sed do</h3>
<p class="abs" style="left:629px;top:2517px;width:340px;font-size:14px;line-height:32px;color:var(--text)">Lorem ipsum dolor sit amet, consectetur adipisicing elit, sed do eiusmod tempor incididunt ut labore et dolore magna aliqua. Ut enim.</p>
<div class="btn btn-sm abs" style="left:626px;top:2638px">Read More</div>
<div class="photo abs" style="left:1046px;top:2372px;width:154px;height:315px;background:radial-gradient(circle at 60% 50%,#7fd3ff,#1a5d99 55%,#0a1f3d)" role="img" aria-label="Digital security shields and padlock graphic"></div>

<section class="contact abs"></section>
<h2 class="contact-title abs">CONTACT US</h2>
<div class="field abs" style="left:230px;top:3005px;width:363px;height:45px">First Name</div>
<div class="field abs" style="left:605px;top:3005px;width:363px;height:45px">Last Name</div>
<div class="field abs" style="left:230px;top:3072px;width:738px;height:45px">Email</div>
<div class="field abs" style="left:230px;top:3136px;width:738px;height:114px">Message</div>
<div class="btn-submit abs">SUBMIT</div>
<div class="chat abs">
  <svg width="44" height="38" viewBox="0 0 44 38"><path d="M4 4 H40 V28 H18 L8 36 V28 H4 Z" fill="#fff"/><circle cx="14" cy="16" r="3" fill="#111"/><circle cx="22" cy="16" r="3" fill="#111"/><circle cx="30" cy="16" r="3" fill="#111"/></svg>
</div>

<footer class="site-footer abs"></footer>
<div class="brand abs" style="left:76px;top:3440px"><span class="dot"></span><span class="name" style="font-size:48px">Vaultmerrow</span></div>
<nav class="fnav">
  <a style="left:626px">Home</a>
  <a style="left:731px">Services</a>
  <a style="left:816px">About</a>
  <a style="left:911px">Resources</a>
  <a style="left:994px">Blog</a>
  <a style="left:1079px">Contact Us</a>
</nav>
<span class="social abs" style="left:1012px"></span>
<span class="social abs" style="left:1057px"></span>
<span class="social abs" style="left:1104px"></span>
<p class="copyright abs">© 2019 | www.vaultmerrow.com.au</p>

</body>
</html>
```